Letterhead Design for Law Firm

**Edit: I have added the photo of a bottom that I like.

------
We are looking for a re-design of our new letterhead. The letterhead is for a law firm and will be used for digital and traditionally printed correspondence.

Here are some suggestions:

- Please use colours are #8ec900 and simple black.
- Please do not use any type of "waves" at the bottom of the page. This is not in style at all.
- Please stay modern yet conservative.
- Please use font Segoe UI Light or similar if you can
- Avoid clipart or illustrations.
- Utilize ample white space in the layout so the design looks clean and information is easy to read at a glance. Don't overcrowd the letterhead.
- Make sure the letterhead design is consistent with our brand identity (see corvelith.ca)
-Please, no black headers or footers.

I am attaching my current letterhead and signature for your convenience.

Remember, the letterhead is an extension of our professional identity. We are a successful firm and trial lawyers who correspond with insurers, judges, lawyers, courts, clients, etc. Make it new, modern, attractive, yet powerful and conservative.

It needs to be easily printable. I would like the bleed removed in print so the black bar the bottom crosses the page (but the text is not near the edges)
Updates

Low design quality

Target Market(s)

Clients, Government Offices, Judiciary, Lawyers, Insurance Companies, Colleagues.

Industry/Entity Type

Law

Other font styles liked:
• Segoe UI LIght, Calibri Light,

Colors
00AB8E
00BBA5
67D7C9
C6EFE9
E9F9F6

Requirements
Must have
• Everything that is on the letterhead now.
Nice to have
• Cutting Edge design, yet conservative.
Should not have
• law firm cliche design, images,

```html
<!DOCTYPE html>
<html lang="en">
<head>
<meta charset="utf-8">
<title>Corvelith Letterhead</title>
<link rel="stylesheet" href="https://fonts.googleapis.com/css2?family=Open+Sans:wght@300;400&display=swap">
<style>
  :root {
    --brand-green: #8ec900;
    --ink: #1a1a1a;
    --paper: #ffffff;
    --backdrop: #d9d9d9;
  }
  * { margin: 0; padding: 0; box-sizing: border-box; }
  html, body {
    width: 1200px;
    height: 848px;
    overflow: hidden;
    background: var(--backdrop);
    font-family: "Open Sans", "Segoe UI", sans-serif;
  }
  .letterhead {
    position: absolute;
    left: 291px;
    top: 24px;
    width: 618px;
    height: 800px;
    background: var(--paper);
    box-shadow: 0 2px 10px rgba(0,0,0,0.18);
  }
  .top-band {
    position: absolute;
    top: 0; left: 0; right: 0;
    height: 6px;
    background: var(--brand-green);
  }
  .bottom-band {
    position: absolute;
    bottom: 0; left: 0; right: 0;
    height: 10px;
    background: var(--brand-green);
  }
  .footer {
    position: absolute;
    right: 40px;
    bottom: 34px;
    display: flex;
    align-items: flex-end;
    gap: 26px;
    color: var(--ink);
  }
  .firm-name {
    display: flex;
    flex-direction: column;
    align-items: flex-start;
  }
  .firm-name .name {
    font-weight: 400;
    font-size: 30px;
    letter-spacing: 1px;
    line-height: 1;
  }
  .firm-name .practice {
    margin-top: 5px;
    font-weight: 400;
    font-size: 8.5px;
    letter-spacing: 1.6px;
    text-transform: uppercase;
  }
  .address, .contact {
    font-weight: 300;
    font-size: 10.5px;
    line-height: 1.45;
    font-style: normal;
  }
</style>
</head>
<body>
  <main class="letterhead">
    <div class="top-band"></div>
    <footer class="footer">
      <div class="firm-name">
        <span class="name">CORVELITH</span>
        <span class="practice">Personal Injury Lawyers</span>
      </div>
      <address class="address">
        48 Harbour Row<br>
        Suite 900, Lakeport<br>
        ON K2B 7M3, Canada
      </address>
      <address class="contact">
        555-214-0377<br>
        info@corvelith.ca<br>
        corvelith.ca
      </address>
    </footer>
    <div class="bottom-band"></div>
  </main>
</body>
</html>
```